Business Card Design Project

We are a construction company in Orange County, CA. We need a two sided business card. We would like the back to be our logo with web URL. Front should included Name, title, address, phone, fax and email address.

our address is
627 West Dorrance Blvd, Suite 308
Anaheim, CA 92718

Our logo files are attached.

Construction

```html
<!DOCTYPE html>
<html lang="en">
<head>
<meta charset="utf-8">
<title>Orvek Business Card</title>
<link rel="stylesheet" href="https://fonts.googleapis.com/css2?family=Source+Sans+3:wght@400;600;700;900&display=swap">
<style>
  :root {
    --brand-blue: #1b4a7d;
    --ink: #3a3a3a;
    --card: #ffffff;
    --backdrop: #ececec;
    --card-edge: #d4d4d4;
  }
  * { margin: 0; padding: 0; box-sizing: border-box; }
  html, body {
    width: 1200px; height: 1136px; overflow: hidden;
    background: var(--backdrop);
    font-family: "Source Sans 3", Arial, sans-serif;
  }
  .canvas { position: relative; width: 1200px; height: 1136px; }
  .card {
    position: absolute; background: var(--card);
    border: 1px solid var(--card-edge); border-radius: 30px; overflow: hidden;
  }
  .card--front { left: 72px; top: 87px; width: 803px; height: 458px; }
  .card--back { left: 331px; top: 602px; width: 802px; height: 458px; }

  .brand-name {
    color: var(--brand-blue); font-weight: 900; line-height: 1;
    letter-spacing: -1px;
  }
  .card--front .brand-name {
    position: absolute; left: 38px; top: 34px; font-size: 118px;
  }
  .divider {
    position: absolute; left: 0; top: 196px; width: 500px; height: 2px;
    background: var(--brand-blue);
  }
  .name-tab {
    position: absolute; left: 483px; top: 161px; width: 320px; height: 70px;
    background: var(--brand-blue); border-radius: 35px 0 0 35px;
    box-shadow: 0 8px 10px -6px rgba(27,74,125,0.45);
    color: #fff; font-size: 28px; display: flex; align-items: center;
    padding-left: 54px;
  }
  .name-tab .person { font-weight: 700; }
  .contact-list {
    position: absolute; left: 38px; top: 234px; list-style: none;
    color: var(--ink); font-size: 20px; line-height: 25px;
  }
  .contact-list li { display: flex; align-items: center; gap: 8px; }
  .contact-list svg { width: 16px; height: 16px; fill: var(--ink); flex: none; }
  .address {
    position: absolute; left: 38px; top: 357px; color: var(--ink);
    font-size: 20px; line-height: 25px; font-style: normal;
  }

  .card--back .brand-name {
    position: absolute; left: 0; right: 0; top: 150px; text-align: center;
    font-size: 132px;
  }
  .back-url {
    position: absolute; left: 0; right: 0; top: 327px; text-align: center;
    color: #4a4a4a; font-size: 27px; letter-spacing: 2px;
  }
</style>
</head>
<body>
<main class="canvas">
  <section class="card card--front">
    <div class="brand-name">ORVEK</div>
    <div class="divider"></div>
    <div class="name-tab"><span class="person">Your Name,</span>&nbsp;Title</div>
    <ul class="contact-list">
      <li><svg viewBox="0 0 16 16"><path d="M3 1l3 3-2 2c1 2 3 4 5 5l2-2 3 3-2 3C6 15 1 10 1 3z"/></svg>714-555-0142</li>
      <li><svg viewBox="0 0 16 16"><path d="M4 1h8v4H4zM1 6h14v7h-3v2H4v-2H1zM5 11v3h6v-3z"/></svg>714-555-0143</li>
      <li><svg viewBox="0 0 16 16"><path d="M1 4h14v9H1zM2 5l6 4 6-4z" fill-rule="evenodd"/></svg>info@orvekbuild.com</li>
      <li><svg viewBox="0 0 16 16"><circle cx="8" cy="8" r="7"/><path d="M1 8h14M8 1c-3 4-3 10 0 14M8 1c3 4 3 10 0 14" stroke="#fff" stroke-width="1" fill="none"/></svg>www.orvekbuild.com</li>
    </ul>
    <address class="address">627 West Dorrance Blvd<br>Suite 308, Anaheim, CA&nbsp; 92718</address>
  </section>

  <section class="card card--back">
    <div class="brand-name">ORVEK</div>
    <div class="back-url">www.orvekbuild.com</div>
  </section>
</main>
</body>
</html>
```